New business card design

I need original, modern, business looking but dzen (minimalistic) looking design.
Also refer to websit travenko.ru

Text is

Веденин Олег, PMP
Партнер

Моб. +7 (915) 604 7189
info@travenko.ru
Москва, Россия, 125493, ул. Берёзовая 27/2
=====================

Vedenin Oleg, PMP
Partner

Mob. +7 (915) 604 7189
info@travenko.ru
Moscow, Russia,125493, Beryozovaya 27/2

```html
<!DOCTYPE html>
<html lang="en">
<head>
<meta charset="utf-8">
<title>Travenko business card</title>
<link rel="stylesheet" href="https://fonts.googleapis.com/css2?family=Exo+2:wght@300;400;500&display=swap">
<style>
  :root {
    --page: #e9ebee;
    --card-top: #ffffff;
    --card-bottom: #e6e7e9;
    --brand-blue: #2b83c6;
    --accent-blue: #2b83c6;
    --ink: #3a3d42;
    --rule: #55595f;
    --on-blue: #ffffff;
  }
  * { margin: 0; padding: 0; box-sizing: border-box; }
  html, body {
    width: 1200px; height: 900px; overflow: hidden;
    background: var(--page);
    font-family: "Exo 2", sans-serif;
  }
  .canvas { position: relative; width: 1200px; height: 900px; }
  .card {
    position: absolute; left: 260px; width: 680px; height: 390px;
    border-radius: 30px; overflow: hidden;
    background: linear-gradient(160deg, var(--card-top) 30%, var(--card-bottom));
    box-shadow: 0 6px 22px rgba(0,0,0,.12);
  }
  .card--front { top: 45px; }
  .card--back { top: 465px; }
  .card__wave { position: absolute; inset: 0; }

  .brand { position: absolute; display: flex; align-items: center; gap: 14px; color: var(--ink); font-weight: 300; }
  .brand__mark { background: var(--brand-blue); }
  .card--front .brand { left: 330px; top: 62px; font-size: 50px; }
  .card--front .brand__mark { width: 40px; height: 40px; }
  .card--back .brand { left: 50%; top: 50%; transform: translate(-50%, -50%); font-size: 84px; }
  .card--back .brand__mark { width: 64px; height: 64px; }

  .person { position: absolute; left: 40px; top: 92px; }
  .person__name { color: var(--accent-blue); font-size: 22px; font-weight: 500; letter-spacing: 1.5px; text-transform: uppercase; }
  .person__role { color: var(--ink); font-size: 15px; letter-spacing: 1.5px; text-transform: uppercase; margin-top: 2px; }

  .address { position: absolute; left: 40px; top: 186px; color: var(--on-blue); font-size: 17px; line-height: 1.5; letter-spacing: .5px; }

  .contacts { position: absolute; right: 36px; top: 282px; list-style: none; color: var(--on-blue); font-size: 14px; letter-spacing: .5px; text-align: right; }
  .contacts li { display: flex; align-items: center; justify-content: flex-end; gap: 8px; height: 25px; }
  .contacts svg { width: 13px; height: 13px; fill: none; stroke: var(--on-blue); stroke-width: 1.8; }
</style>
</head>
<body>
<main class="canvas">
  <section class="card card--front" aria-label="Business card front">
    <svg class="card__wave" viewBox="0 0 680 390" preserveAspectRatio="none" aria-hidden="true">
      <defs>
        <linearGradient id="rule-fade" x1="0" y1="0" x2="1" y2="0">
          <stop offset="0.25" stop-color="var(--rule)" stop-opacity="0"/>
          <stop offset="0.6" stop-color="var(--rule)" stop-opacity="1"/>
        </linearGradient>
      </defs>
      <path d="M0,138 C220,148 450,203 680,253" stroke="url(#rule-fade)" stroke-width="5" fill="none"/>
      <path d="M0,150 C220,160 450,215 680,265 L680,390 L0,390 Z" fill="var(--brand-blue)"/>
    </svg>
    <div class="brand"><span class="brand__mark"></span>Travenko</div>
    <div class="person">
      <p class="person__name">Vedenin Oleg</p>
      <p class="person__role">Partner</p>
    </div>
    <p class="address">Beryozovaya 27/2<br>Moscow, 125493</p>
    <ul class="contacts">
      <li>+7 (915) 604 7189
        <svg viewBox="0 0 16 16"><path d="M4 2l2 3-1.5 1.5a8 8 0 0 0 5 5L11 10l3 2-1 2c-6 0-11-5-11-11z"/></svg></li>
      <li>info@travenko.ru
        <svg viewBox="0 0 16 16"><rect x="2" y="4" width="12" height="8"/><path d="M2 4l6 5 6-5"/></svg></li>
      <li>www.travenko.ru
        <svg viewBox="0 0 16 16"><circle cx="8" cy="8" r="6"/><path d="M2 8h12M8 2c3 3 3 9 0 12M8 2c-3 3-3 9 0 12"/></svg></li>
    </ul>
  </section>

  <section class="card card--back" aria-label="Business card back">
    <div class="brand"><span class="brand__mark"></span>Travenko</div>
  </section>
</main>
</body>
</html>
```